Tidal Forge - Crypto Currency Miner Powered by Renewable Energy Website

We Need Web Pages Design for Website for Crypto Currency Miner

Serivices include:
Mining Rig Sales
Housing for Rigs turnkey on renewable energy grid
Cloud Mining term packages
Updates

http://www.vaultrigsurvey.example (Competitors sites)

Target Market(s)

Investers for Mining Rigs and terms for 1,2 or 3 years of Hash rate

Industry/Entity Type

Mining

Number of Pages Required

5+ page

Font styles to use
Sans Serif

Colors
add136
9bcb3c
606060
474747
ffc214
cadf82
fbee3e
876aae
6b449b

Requirements
Must have
• Pictures of Solar, Wind and power Factor Correction units
Nice to have
• e-commerce platform so contract terms can be purchased through website
Should not have
• Heavy construction equipment

```html
<!DOCTYPE html>
<html lang="en">
<head>
<meta charset="utf-8">
<title>Tidal Forge – Renewable Crypto Mining</title>
<link href="https://fonts.googleapis.com/css2?family=Oswald:wght@300;400;500&family=Open+Sans:wght@400;600&display=swap" rel="stylesheet">
<style>
:root{
  --green:#9bcb3c;
  --green-bright:#add136;
  --green-pale:#cadf82;
  --yellow:#ffc214;
  --lemon:#fbee3e;
  --gray:#606060;
  --dark:#474747;
  --light:#f1f1f1;
  --white:#ffffff;
}
*{box-sizing:border-box;margin:0;padding:0}
html,body{width:1200px;height:4036px;overflow:hidden}
body{font-family:"Open Sans",Arial,sans-serif;color:var(--gray);background:var(--white);position:relative}
.head{font-family:"Oswald",Arial,sans-serif}
section,header,footer{position:absolute;left:0;width:1200px;overflow:hidden}

/* header */
.site-header{top:0;height:100px;background:var(--white);border-top:6px solid var(--green)}
.brand{position:absolute;left:220px;top:22px;display:flex;align-items:center;gap:10px}
.brand-dot{width:34px;height:34px;border-radius:50%;background:var(--green)}
.brand-name{font-family:"Oswald",sans-serif;font-size:24px;font-weight:400;color:var(--dark)}
.main-nav{position:absolute;left:450px;top:0;display:flex;height:90px;align-items:center}
.main-nav a{font-family:"Oswald",sans-serif;font-size:15px;color:var(--dark);text-decoration:none;padding:0 13px;height:64px;line-height:64px;text-transform:uppercase}
.main-nav a.active{background:var(--yellow);color:var(--white)}

/* hero */
.hero{top:100px;height:726px}
.hero-photo{position:absolute;inset:0;background:radial-gradient(ellipse at 55% 55%,#f6f39a 0%,#d8e35a 22%,#9bbd2c 48%,#4d6a18 78%,#2e3e10 100%)}
.hero-panel{position:absolute;left:627px;top:0;width:423px;height:726px;background:rgba(255,255,255,.9);text-align:center;padding:88px 30px 0}
.hero-kicker{font-size:15px;line-height:22px;color:var(--dark)}
.hero-title{font-family:"Oswald",sans-serif;font-weight:400;font-size:74px;line-height:84px;color:var(--dark);margin:16px 0 22px;text-transform:uppercase}
.hero-text{font-size:15px;line-height:22px;color:var(--dark);padding:0 8px}
.btn-start{display:inline-block;margin-top:28px;background:var(--green);color:var(--white);font-family:"Oswald",sans-serif;font-size:24px;padding:8px 26px;border-radius:4px}
.hero-rule{width:360px;height:1px;background:#bbb;margin:28px auto 0}
.hero-auth{display:flex;justify-content:space-between;margin:32px 14px 0}
.hero-auth span{width:175px;height:44px;line-height:44px;font-family:"Oswald",sans-serif;font-size:22px;color:var(--white);border-radius:3px}
.sign-in{background:var(--yellow)}
.sign-up{background:var(--dark)}

/* features */
.features{top:826px;height:511px;background:var(--white)}
.feature{position:absolute;top:80px;width:260px;text-align:center}
.feature svg{width:80px;height:80px;stroke:var(--green);fill:none;stroke-width:2.5}
.feature h3{font-family:"Oswald",sans-serif;font-weight:300;font-size:26px;line-height:32px;color:var(--dark);margin:36px 0 16px;text-transform:uppercase}
.feature p{font-size:13px;line-height:18px;color:var(--dark)}
.btn-outline{display:inline-block;margin-top:16px;border:2px solid var(--green);color:var(--dark);font-size:13px;padding:5px 30px;border-radius:3px}
.btn-solid{background:var(--green);color:var(--white)}

/* about */
.about{top:1337px;height:568px;background:linear-gradient(100deg,var(--green) 0%,var(--green-bright) 60%,var(--green-pale) 100%)}
.about-copy{position:absolute;left:175px;top:70px;width:350px;color:var(--white)}
.about-copy h2{font-family:"Oswald",sans-serif;font-weight:400;font-size:40px;margin-bottom:20px}
.lead{font-family:"Oswald",sans-serif;font-weight:300;font-size:20px;line-height:26px;margin-bottom:24px}
.about-copy p.small{font-size:12px;line-height:17px;margin-bottom:18px}
.btn-white{display:inline-block;margin-left:220px;border:2px solid var(--white);color:var(--white);font-size:13px;padding:4px 24px;border-radius:3px}
.about-art{position:absolute;left:630px;top:90px;width:420px;height:420px;border-radius:50%;background:radial-gradient(circle,#6f9a20 0%,#7fa92a 60%,rgba(155,203,60,0) 72%)}

/* testimonials */
.testimonials{top:1905px;height:363px;background:var(--light)}
.section-title{font-family:"Oswald",sans-serif;font-weight:400;font-size:36px;color:var(--green);text-align:center}
.testimonials .section-title{margin-top:52px}
.quote{position:absolute;top:140px;width:418px;height:182px;background:var(--white);box-shadow:0 6px 14px rgba(0,0,0,.25);padding:20px 22px}
.quote p{font-size:12px;line-height:17px;color:var(--dark);width:260px}
.quote .who{margin-top:18px;font-size:12px;line-height:16px}
.quote .who b{font-weight:600}
.avatar{position:absolute;right:26px;top:70px;width:78px;height:78px;border-radius:50%;background:linear-gradient(#d6d6d6,#9a9a9a);border:4px solid #e8e8e8}

/* why */
.why{top:2268px;height:584px;background:var(--white)}
.tile{position:absolute;width:183px;height:183px;border-radius:12px;text-align:center;padding-top:26px}
.tile svg{width:82px;height:82px;stroke:var(--white);fill:none;stroke-width:3}
.tile span{display:block;font-family:"Oswald",sans-serif;font-size:23px;line-height:26px;color:var(--white);margin-top:12px}
.tile.dark-text svg{stroke:var(--dark)}
.tile.dark-text span{color:var(--dark)}
.why-copy{position:absolute;left:670px;top:90px;width:370px;color:var(--dark)}
.why-copy h2{font-family:"Oswald",sans-serif;font-weight:400;font-size:36px;color:var(--green);margin-bottom:18px}
.why-copy .lead{color:var(--dark);font-size:19px;line-height:25px;margin-bottom:20px}
.why-copy p.small{font-size:12px;line-height:17px;margin-bottom:16px}
.btn-dark{display:inline-block;margin-left:250px;border:2px solid var(--gray);color:var(--dark);font-size:13px;padding:4px 24px;border-radius:3px}

/* payments */
.payments{top:2852px;height:288px;background:linear-gradient(90deg,#8cc23b,var(--green) 50%,#5fb34d);text-align:center;color:var(--white)}
.payments h2{font-family:"Oswald",sans-serif;font-weight:400;font-size:38px;margin-top:40px}
.card-names{display:flex;justify-content:center;gap:46px;margin-top:34px;align-items:center}
.card-names span{display:flex;align-items:center;gap:10px;font-family:"Oswald",sans-serif;font-size:34px;font-weight:500;color:var(--white)}
.card-names i{width:50px;height:50px;border-radius:50%;background:var(--yellow)}
.payments .btn-white{margin:26px 0 0}

/* video */
.video{top:3140px;height:285px;background:linear-gradient(#f4f4f4,#e4e4e4);text-align:center}
.play{margin-top:36px;width:56px;height:56px}
.video h2{font-family:"Oswald",sans-serif;font-weight:400;font-size:36px;color:var(--dark);margin-top:8px}
.video p{font-size:14px;line-height:20px;color:var(--dark);width:420px;margin:6px auto 0}

/* footer dark */
.footer-main{top:3425px;height:368px;background:var(--dark);color:#ddd}
.f-col{position:absolute;top:60px}
.f-col h4{font-family:"Oswald",sans-serif;font-weight:400;font-size:26px;color:var(--yellow);margin-bottom:18px}
.f-col p{font-size:14px;line-height:20px;width:200px}
.btn-y{display:block;width:155px;margin-top:18px;border:2px solid var(--yellow);color:var(--yellow);text-align:center;font-size:14px;padding:3px 0;border-radius:3px}
.socials{display:grid;grid-template-columns:repeat(3,30px);gap:10px 12px;margin-top:28px}
.socials i{width:30px;height:30px;border-radius:50%;border:2px solid #ccc}
.f-links{position:absolute;left:648px;top:168px;display:grid;grid-template-columns:130px 140px 110px;row-gap:12px}
.f-links a{font-family:"Oswald",sans-serif;font-size:16px;color:#eee;text-decoration:none;text-transform:uppercase}

/* footer yellow */
.footer-bottom{top:3793px;height:243px;background:var(--yellow);color:var(--white)}
.footer-brand{position:absolute;left:196px;top:80px;display:flex;align-items:center;gap:10px}
.footer-brand i{width:34px;height:34px;border-radius:50%;background:var(--white)}
.footer-brand span{font-family:"Oswald",sans-serif;font-size:24px;color:var(--white)}
.accept{position:absolute;left:412px;top:80px;font-size:13px}
.accept .mini{display:flex;gap:14px;margin-bottom:20px;font-family:"Oswald",sans-serif;font-size:14px}
.addr{position:absolute;top:80px;font-size:14px;line-height:19px;width:170px}
</style>
</head>
<body>

<header class="site-header">
  <div class="brand"><span class="brand-dot"></span><span class="brand-name">Tidal Forge</span></div>
  <nav class="main-nav">
    <a href="#">Home</a><a href="#">Blog</a><a href="#" class="active">Pricing</a><a href="#">Our Offer</a><a href="#">About Us</a><a href="#">Press</a><a href="#">Customer Service</a><a href="#">Datacenters</a>
  </nav>
</header>

<section class="hero">
  <div class="hero-photo" role="img" aria-label="Wind turbines silhouetted against a glowing yellow-green sunset sky"></div>
  <div class="hero-panel">
    <p class="hero-kicker">Join over 1.000.000 people with the world's<br>leading hashpower provider</p>
    <h1 class="hero-title">Start<br>Tidal Forge<br>Today!</h1>
    <p class="hero-text">It's super simple - Your mining rigs are already set up and running. As soon as you've set up your account you can start to earn your first coins from our bitcoin cloud mining service!</p>
    <span class="btn-start">Start Mining Now!</span>
    <div class="hero-rule"></div>
    <div class="hero-auth"><span class="sign-in">SIGN IN</span><span class="sign-up">SIGN UP</span></div>
  </div>
</section>

<section class="features">
  <div class="feature" style="left:201px">
    <svg viewBox="0 0 80 80"><circle cx="40" cy="40" r="36"/><circle cx="40" cy="38" r="4"/><path d="M40 34 L38 12 M43 41 L62 50 M37 41 L20 52 M40 42 L40 70"/></svg>
    <h3>Wind Power<br>Investment</h3>
    <p>Don't wrestle with rig assembly and hot, noisy miners at home. We have the fastest bitcoin mining hardware running for you already!</p>
    <span class="btn-outline">Learn More</span>
  </div>
  <div class="feature" style="left:470px">
    <svg viewBox="0 0 80 80"><circle cx="40" cy="10" r="5"/><path d="M16 30 H64 L70 56 H10 Z M28 30 L25 56 M52 30 L55 56 M13 43 H67 M40 30 V56 M40 56 V72 M28 72 H52"/></svg>
    <h3>Solar Power<br>Investment</h3>
    <p>Don't wrestle with rig assembly and hot, noisy miners at home. We have the fastest bitcoin mining hardware running for you already!</p>
    <span class="btn-outline btn-solid">Learn More</span>
  </div>
  <div class="feature" style="left:739px">
    <svg viewBox="0 0 80 80"><rect x="10" y="24" width="60" height="44" rx="5"/><path d="M16 24 L52 10 L58 24 M50 40 H70 V54 H50 Z"/><circle cx="57" cy="47" r="2"/></svg>
    <h3>Get Your First<br>Payout Today</h3>
    <p>Don't wrestle with rig assembly and hot, noisy miners at home. We have the fastest bitcoin mining hardware running for you already!</p>
    <span class="btn-outline">Learn More</span>
  </div>
</section>

<section class="about">
  <div class="about-copy">
    <h2>About Tidal Forge?</h2>
    <p class="lead">Lorem ipsum dolor sit amet, consectetur adipisicing elit. Aliquam praesentium, distinctio dicta molestias dignissimos.</p>
    <p class="small">Our rigs run in sealed halls fed by wind and solar farms. Each unit is tuned for steady hash output, cooled by outside air and watched day and night by our team.</p>
    <p class="small">Contracts run for one, two or three years. You choose the hash rate, we handle power, upkeep and payouts, and you follow every coin from a clear daily dashboard.</p>
    <span class="btn-white">Learn More</span>
  </div>
  <div class="about-art" role="img" aria-label="Green globe surrounded by wind turbines, solar panels, trees and city buildings"></div>
</section>

<section class="testimonials">
  <h2 class="section-title">What People Are Saying</h2>
  <div class="quote" style="left:175px">
    <p>OreNorth is very happy to have Northwind Hash as our trustworthy partner. We have already recommended Northwind Hash to thousands of our existing customers who are happy and satisfied with their excellent services and products.</p>
    <p class="who"><b>Lena Varo</b>, CEO of OreNorth<br>Official Distribution Partner of Tidal Forge</p>
    <div class="avatar" role="img" aria-label="Portrait photo of the reviewer"></div>
  </div>
  <div class="quote" style="left:613px">
    <p>OreNorth is very happy to have Northwind Hash as our trustworthy partner. We have already recommended Northwind Hash to thousands of our existing customers who are happy and satisfied with their excellent services and products.</p>
    <p class="who"><b>Lena Varo</b>, CEO of OreNorth<br>Official Distribution Partner of Tidal Forge</p>
    <div class="avatar" role="img" aria-label="Portrait photo of the reviewer"></div>
  </div>
</section>

<section class="why">
  <div class="tile" style="left:175px;top:89px;background:var(--green)">
    <svg viewBox="0 0 80 80"><path d="M40 6 L68 16 V38 C68 56 55 68 40 74 C25 68 12 56 12 38 V16 Z"/><circle cx="40" cy="36" r="8"/><path d="M40 44 V56"/></svg>
    <span>Safe And Secure</span>
  </div>
  <div class="tile" style="left:403px;top:89px;background:var(--yellow)">
    <svg viewBox="0 0 80 80"><rect x="18" y="8" width="32" height="64" rx="5"/><path d="M30 64 H38"/><circle cx="58" cy="36" r="9"/><circle cx="58" cy="36" r="3"/></svg>
    <span>Mobile App</span>
  </div>
  <div class="tile dark-text" style="left:175px;top:304px;background:var(--lemon)">
    <svg viewBox="0 0 80 80"><rect x="10" y="22" width="60" height="46" rx="5"/><path d="M14 22 L50 10 L56 22 M50 38 H70 V52 H50 Z"/></svg>
    <span>Secure Wallet</span>
  </div>
  <div class="tile dark-text" style="left:403px;top:304px;background:#eaf2d2">
    <svg viewBox="0 0 80 80"><rect x="16" y="12" width="48" height="60" rx="4"/><path d="M30 8 H50 V16 H30 Z M40 28 L54 33 V44 C54 52 48 57 40 60 C32 57 26 52 26 44 V33 Z"/></svg>
    <span>Covered By<br>Insurance</span>
  </div>
  <div class="why-copy">
    <h2>Why Choose Tidal Forge?</h2>
    <p class="lead">Lorem ipsum dolor sit amet, consectetur adipisicing elit. Aliquam praesentium, distinctio dicta molestias dignissimos.</p>
    <p class="small">Every contract is backed by metered green power and insured hardware. Payouts arrive daily in your wallet with no hidden fees or setup costs.</p>
    <p class="small">Track hash rate, uptime and earnings from any device. Our support team answers within hours and our data centers report their energy mix every month.</p>
    <span class="btn-dark">Learn More</span>
  </div>
</section>

<section class="payments">
  <h2>Creditcard payments available.</h2>
  <div class="card-names">
    <span><i></i>CardOne</span>
    <span>PayLine</span>
  </div>
  <span class="btn-white">Try IT Now!</span>
</section>

<section class="video">
  <svg class="play" viewBox="0 0 56 56"><circle cx="28" cy="28" r="25" fill="none" stroke="#9bcb3c" stroke-width="4"/><path d="M22 16 L40 28 L22 40 Z" fill="#9bcb3c"/></svg>
  <h2>Video Review</h2>
  <p>Various versions have evolved over the years, sometimes by accident, sometimes on purpose (injected humour and the like).</p>
</section>

<footer class="footer-main">
  <div class="f-col" style="left:190px">
    <h4>Member Area</h4>
    <p>If you don't have an account, sign up for free.</p>
    <span class="btn-y" style="margin-top:34px">SIGN UP</span>
    <span class="btn-y">LOGIN</span>
  </div>
  <div class="f-col" style="left:430px">
    <h4>Follow us</h4>
    <p>Stay up to date with Tidal Forge activities.</p>
    <div class="socials"><i></i><i></i><i></i><i></i><i></i><i></i></div>
  </div>
  <nav class="f-links">
    <a href="#">Home</a><a href="#">About Us</a><a href="#">Privacy</a>
    <a href="#">Pricing</a><a href="#">Datacenter</a><a href="#">Contact</a>
    <a href="#">Our Offer</a><a href="#">Press</a><span></span>
  </nav>
</footer>

<footer class="footer-bottom">
  <div class="footer-brand"><i></i><span>Tidal Forge</span></div>
  <div class="accept">
    <div class="mini"><span>CardOne</span><span>PayLine</span><span>NetPurse</span></div>
    We accept creditcard payment
  </div>
  <div class="addr" style="left:638px">Address<br>Tidal Forge<br><br>Address line here address line here Address line here</div>
  <div class="addr" style="left:850px">Address<br>Tidal Forge<br><br>Address line here Address line here Address line here</div>
</footer>

</body>
</html>
```